Glen Whitmore Professional Coaching

I would like a website with a mountain theme geared towards professional executives reaching higher peaks and goals. This is a 3 page website with brand essence information on the opening page, the coaching process on a second page and "about me" and lead capture form on a third page

Target Market(s)

C-Level audience, involved in tech, government, manufacturing, and transportation type of corporations

Coding

Coded - Design and coding required

Number of Pages Required

3 page

Font styles to use
Sans Serif

Colors
a7a7a7
1b1b1b
e8e8e8
3176b5
abd036
0355a3

Requirements
Must have
• Looking for a user friendly site that I can manage/update going forward. Must have:
• 1. "Is coaching right for you?" - page 1
• 2. "Our Process" page 2 - I will describe how we approach coaching
• 3. "Contact us" page 3 where I can capture contact information from potential clients
• 4. Clean and professional with more modern font
• 5. Links to personal social media sites
• 6. Ability to upload/download .pdf documents as resources
• 7. Ability to add on new pages in the future (such as a blog page)
Nice to have
• I want a place to store articles I write or use.
• LinkedIn or Twitter Feed
Should not have
• Not fluffy or too 'zen' like personal life coaches tend to present.

```html
<!DOCTYPE html>
<html lang="en">
<head>
<meta charset="utf-8">
<title>Glen Whitmore Professional Coaching</title>
<link rel="stylesheet" href="https://fonts.googleapis.com/css2?family=Roboto:wght@400;500;700&family=Open+Sans:wght@400;600;700&display=swap">
<style>
  :root {
    --ink: #1b1b1b;
    --grey: #a7a7a7;
    --mist: #e8e8e8;
    --blue: #3176b5;
    --navy: #0355a3;
    --brand-blue: #1f5fb5;
    --section-tint: #eff4f4;
    --footer: #2a2a2a;
    --body-text: #555555;
    --white: #ffffff;
  }
  * { box-sizing: border-box; margin: 0; padding: 0; }
  html, body { width: 1200px; height: 3232px; overflow: hidden; }
  body { position: relative; background: var(--white); font-family: "Open Sans", Arial, sans-serif; color: var(--ink); }
  .abs { position: absolute; }

  /* Header */
  .site-header { position: absolute; left: 0; top: 0; width: 1200px; height: 120px; z-index: 3; }
  .brand { left: 112px; top: 30px; font-family: "Roboto", Arial, sans-serif; font-weight: 700; font-size: 56px; line-height: 68px; color: var(--ink); }
  .main-nav { right: 108px; top: 50px; display: flex; align-items: center; gap: 36px; font-family: "Roboto", Arial, sans-serif; font-size: 18px; font-weight: 500; }
  .main-nav a { color: var(--ink); text-decoration: none; }
  .main-nav a.is-active { color: var(--brand-blue); }

  /* Hero */
  .hero-photo {
    left: 0; top: 0; width: 1200px; height: 740px;
    clip-path: polygon(0 300px, 534px 409px, 872px 120px, 100% 120px, 100% 100%, 0 100%);
    background:
      linear-gradient(180deg, rgba(0,0,0,0) 68%, #56733a 80%, #6e9438 100%),
      linear-gradient(100deg, #b9c3d0 0%, #7d8a9c 38%, #5f8fd6 55%, #8dbbef 100%);
  }
  .hero-title { left: 726px; top: 288px; width: 440px; font-family: "Roboto", Arial, sans-serif; font-weight: 500; font-size: 38px; line-height: 56px; color: var(--white); }
  .btn-outline-light { left: 726px; top: 494px; width: 200px; height: 56px; border: 2px solid var(--white); border-radius: 28px; color: var(--white); font-family: "Roboto", Arial, sans-serif; font-weight: 700; font-size: 16px; display: flex; align-items: center; justify-content: center; letter-spacing: .5px; }

  /* About */
  .about-portrait { left: 110px; top: 888px; width: 430px; height: 430px; border-radius: 50%; background: radial-gradient(circle at 50% 40%, #6d8a78 0%, #3b5a45 45%, #22344f 80%); }
  .eyebrow { font-family: "Roboto", Arial, sans-serif; font-weight: 700; font-size: 28px; color: var(--brand-blue); }
  .section-title { font-family: "Roboto", Arial, sans-serif; font-weight: 700; font-size: 52px; color: var(--ink); letter-spacing: .5px; }
  .body-copy { font-size: 14px; line-height: 29px; color: var(--body-text); }
  .btn-outline { width: 174px; height: 60px; border: 2px solid var(--brand-blue); border-radius: 30px; color: var(--brand-blue); font-family: "Roboto", Arial, sans-serif; font-weight: 700; font-size: 17px; display: flex; align-items: center; justify-content: center; }

  /* Services */
  .services { left: 0; top: 1422px; width: 1200px; height: 840px; background: var(--section-tint); overflow: hidden; }
  .services-photo { position: absolute; left: 0; top: 330px; width: 1200px; height: 510px;
    background: linear-gradient(180deg, #eff4f4 0%, #d5dfe5 30%, #b5c3cc 55%, #6f7f8b 78%, #3a4751 100%); }
  .center { left: 0; width: 1200px; text-align: center; }
  .video-frame { left: 403px; top: 1781px; width: 394px; height: 255px; background: linear-gradient(90deg, #1f2226 0%, #2c2f33 45%, #6d6250 60%, #8b7a60 80%, #5e5446 100%); box-shadow: 0 4px 16px rgba(0,0,0,.25); }
  .play-btn { position: absolute; left: 167px; top: 98px; width: 60px; height: 60px; border-radius: 50%; background: rgba(0,0,0,.55); }

  /* Contact */
  .field { border: 1.5px solid #c9c9c9; background: var(--white); font-size: 14px; color: #555; padding: 10px 14px; }
  .btn-solid { left: 536px; top: 2758px; width: 128px; height: 48px; border-radius: 24px; background: var(--brand-blue); color: var(--white); font-family: "Roboto", Arial, sans-serif; font-weight: 700; font-size: 16px; display: flex; align-items: center; justify-content: center; }

  /* Footer */
  .site-footer { left: 0; top: 2912px; width: 1200px; height: 320px; background: linear-gradient(180deg, #2f2f2f 0%, #2a2a2a 50%, #222 100%); overflow: hidden; }
  .social-link { position: absolute; top: 71px; width: 52px; height: 52px; border: 2px solid var(--white); border-radius: 50%; display: flex; align-items: center; justify-content: center; }
  .footer-line { position: absolute; left: 0; width: 1200px; text-align: center; color: var(--white); font-size: 14px; }
  .footer-line .sep { margin: 0 12px; }
  .footer-line svg { vertical-align: -2px; margin-right: 8px; }
</style>
</head>
<body>

<div class="abs hero-photo" role="img" aria-label="Photograph of a snow-capped alpine peak under a blue sky above green meadows"></div>

<header class="site-header">
  <div class="abs brand">Glen<br>Whitmore</div>
  <nav class="abs main-nav">
    <a class="is-active" href="#">Home</a>
    <a href="#">About Me</a>
    <a href="#">Coaching Process</a>
    <a href="#">Contact</a>
    <svg width="18" height="18" viewBox="0 0 18 18" aria-label="Search"><circle cx="7.5" cy="7.5" r="5.5" fill="none" stroke="#1b1b1b" stroke-width="2.4"/><line x1="11.5" y1="11.5" x2="16.5" y2="16.5" stroke="#1b1b1b" stroke-width="2.6" stroke-linecap="round"/></svg>
  </nav>
</header>

<h1 class="abs hero-title">Professional executives reaching higher peaks and goals.</h1>
<div class="abs btn-outline-light">GET MORE INFO</div>

<section class="about">
  <div class="abs about-portrait" role="img" aria-label="Portrait photograph of the coach outdoors"></div>
  <div class="abs eyebrow" style="left:607px; top:880px;">ABOUT ME</div>
  <h2 class="abs section-title" style="left:607px; top:930px;">GLEN WHITMORE</h2>
  <p class="abs body-copy" style="left:607px; top:1020px; width:490px;">Nam libero tempore, cum soluta nobis est eligendi optio cumque nihil pedit quo minus id quod maxime placeat facere possimus, omnis voluptas asume nda est, omnis dolor repellendus. Temporibus autem quibusdam et aut offi ciis debits aut rerum necessitatibus saepe eveniet ut et voluptates repudan dae sint et molestiae earum rerum hic ten.</p>
  <div class="abs btn-outline" style="left:607px; top:1206px;">READ MORE</div>
</section>

<section class="abs services">
  <div class="services-photo" role="img" aria-label="Photograph of a misty mountain range"></div>
</section>
<div class="abs eyebrow center" style="top:1506px;">SERVICES</div>
<h2 class="abs section-title center" style="top:1556px;">COACHING PROCESS</h2>
<p class="abs body-copy" style="left:240px; top:1650px; width:720px; text-align:center;">Nam libero tempore, cum soluta nobis est eligendi optio cumque nihil impedit quo minus id quod maxime placeat facere possimus, omnis voluptas assumenda est, omnis dolor repellendus. Temporibus autem quibusd am et aut officiis debitis aut rerum necessipedit qtatibus saepe eveniet</p>
<div class="abs video-frame" role="img" aria-label="Video still of a speaker addressing an audience">
  <div class="play-btn"><svg width="60" height="60" viewBox="0 0 60 60"><polygon points="24,18 24,42 43,30" fill="#ffffff"/></svg></div>
</div>

<section class="contact">
  <div class="abs eyebrow center" style="top:2363px;">CONTACT</div>
  <h2 class="abs section-title center" style="top:2407px;">GET IN TOUCH</h2>
  <div class="abs field" style="left:258px; top:2516px; width:335px; height:42px;">First Name</div>
  <div class="abs field" style="left:607px; top:2516px; width:335px; height:42px;">Last Name</div>
  <div class="abs field" style="left:258px; top:2570px; width:335px; height:42px;">Email Address</div>
  <div class="abs field" style="left:607px; top:2570px; width:335px; height:42px;">Phone Number</div>
  <div class="abs field" style="left:258px; top:2624px; width:684px; height:80px;">Message</div>
  <div class="abs btn-solid">SUBMIT</div>
</section>

<footer class="abs site-footer" role="contentinfo">
  <a class="social-link" style="left:515px;" aria-label="Social profile one">
    <svg width="20" height="20" viewBox="0 0 20 20"><path d="M8 12l4-4M7 9l-2 2a3 3 0 0 0 4 4l2-2M13 11l2-2a3 3 0 0 0-4-4l-2 2" fill="none" stroke="#fff" stroke-width="2" stroke-linecap="round"/></svg>
  </a>
  <a class="social-link" style="left:573px;" aria-label="Social profile two">
    <svg width="20" height="20" viewBox="0 0 20 20"><path d="M3 4h14v9H8l-4 3v-3H3z" fill="#fff"/></svg>
  </a>
  <a class="social-link" style="left:631px;" aria-label="Social profile three">
    <svg width="20" height="20" viewBox="0 0 20 20"><rect x="3" y="5" width="14" height="10" rx="1" fill="#fff"/><polyline points="3,6 10,11 17,6" fill="none" stroke="#2a2a2a" stroke-width="1.5"/></svg>
  </a>
  <div class="footer-line" style="top:160px;">
    <svg width="12" height="14" viewBox="0 0 12 14"><path d="M6 0a5 5 0 0 0-5 5c0 4 5 9 5 9s5-5 5-9a5 5 0 0 0-5-5zm0 7a2 2 0 1 1 0-4 2 2 0 0 1 0 4z" fill="#fff"/></svg>240 Ridgeview Avenue&nbsp; Suite 300&nbsp; Denver, CO 80202<span class="sep">|</span><svg width="14" height="14" viewBox="0 0 14 14"><path d="M3 0l3 3-2 2c1 2 3 4 5 5l2-2 3 3-2 3C6 14 0 8 0 3z" fill="#fff"/></svg>1 800 555 0142<span class="sep">|</span><svg width="16" height="12" viewBox="0 0 16 12"><rect width="16" height="12" rx="1" fill="#fff"/><polyline points="0,1 8,7 16,1" fill="none" stroke="#2a2a2a" stroke-width="1.5"/></svg>info@glenwhitmore.com
  </div>
  <div class="footer-line" style="top:204px;">Help<span class="sep">|</span>FAQ<span class="sep">|</span>Support<span class="sep">|</span>Sitemap<span class="sep">|</span>Terms Of Use<span class="sep">|</span>Privacy Statement</div>
  <div class="footer-line" style="top:244px;">Glen Whitmore © 2019 All rights reserved.</div>
</footer>

</body>
</html>
```